New Bottle Label for our Velinto Grand Reserva Brandy

Graphic Design Brief
We need a new bottle label for our Brandy Gran Reserva that we want to bring to the market.
Please have a look at all our current bottles and labels and the feel of our company under www.velinto-example.ch. We would like the design to be still different to the rest - as it is not a whisky, not a fruit product, not a spirit like a gin, thus we need to create like a new family, but still fitting in with the rest of the products.
The bottle that we will be using for the brand is a different one than the one that we already have, the design of the bottle is attached with a document.
I have also attached a briefing in regards to Brandy in general for your information.
### 1. What is Brandy?
Brandy is a distilled spirit made from fermented wine or other fruit wines. It is traditionally aged in oak barrels, which gives it its characteristic color and rich flavor. The aging process in oak is essential for developing the aromas and quality of the brandy.
### 2. What is Brandy Reserva?
A Brandy labeled as "Reserva" has undergone a longer aging process, typically at least 2 to 3 years, in oak barrels. This aging gives the brandy a deeper, more complex flavor profile and a darker color. "Reserva" is often an indication of higher quality.
### 3. Who enjoys drinking Brandy?
Brandy is typically favored by those who appreciate a deep, rich tasting experience. This often includes older consumers who value the time-aged complexity of the spirit. However, Brandy is also gaining popularity among younger people, especially through cocktails and modern serving styles.
### 4. Why is Brandy trending?
Brandy is experiencing a resurgence as consumers increasingly value quality and artisanal production methods. Its versatility in cocktails and association with traditional, luxurious experiences have also contributed to its renewed popularity.
### 5. What colors would be associated with Brandy?
The typical colors associated with Brandy are warm gold, amber, and deep golden-brown tones. These colors reflect the aging process in oak barrels and the richness of the flavors. Other associated colors might include dark brown and mahogany.
### 6. What is important to customers when buying Brandy?
Customers care about the origin of the Brandy, the aging time, the quality of the ingredients, the production method, and the brand. They also pay attention to the prestige of the product and the authenticity of the production.
### 7. What is not important to customers when buying Brandy?
For many customers, the price and packaging (unless it’s especially exclusive) may be less important than the quality and taste of the Brandy. The distillery name might be less significant if it isn’t tied to a particular reputation.
### 8. What do customers know about Swiss Brandy?
Swiss Brandy is still relatively unknown in many markets, but customers who are familiar with it appreciate the precision and quality of Swiss production. Swiss Brandy is assumed to be made with care and under strict quality standards.
### 9. What is Brandy Gran Reserva?
**Brandy Gran Reserva** is an even higher quality and longer-aged version of Brandy. Generally, a Gran Reserva is aged for at least 5 to 10 years or more in oak barrels. This extended aging process gives the Brandy an especially deep, complex flavor profile and often a darker, richer color. Gran Reserva is often regarded as the top-tier product within a Brandy range and appeals to discerning consumers who value quality, refinement, and a luxurious tasting experience.
The label “Gran Reserva” thus indicates the highest quality level for Brandies, similar to other spirits (like wine or whisky), where the aging time is a critical factor.
We age our Brandy Gran Reserva in the Solara way.
### 10. What emotions are associated with Brandy?
Brandy is often associated with luxury, relaxation, and comfort. It evokes feelings of tradition, elegance, and sophistication. Drinking Brandy is frequently seen as a moment of reflection and enjoyment.
### 11. How should Brandy be marketed?
Brandy should be marketed with a focus on its artisanal production, quality, and tradition. A narrative around the product, its aging, and origin can help create an emotional connection with the customer. The marketing should also emphasize the versatility of Brandy, whether consumed neat or in cocktails.
**Label design**:
The label should reflect the exclusivity of the product, with an elegant, minimalist design. The label should include information about the aging time, the use of oak barrels, and a brief story about the Brandy’s production.
we would like to have a modern look to the whole deisgn of the brandy
Target Market(s)
Customers that like Brandy
Target Market(s)
Switzerland
Industry/Entity Type
Distillery
Look and feel

```html
<!DOCTYPE html>
<html lang="en">
<head>
<meta charset="utf-8">
<title>Velinto Grand Reserva Brandy – Label</title>
<link rel="stylesheet" href="https://fonts.googleapis.com/css2?family=Zilla+Slab:wght@700&family=Cormorant+Garamond:wght@500&family=Oswald:wght@300&family=Lato:wght@400&display=swap">
<style>
  :root {
    --page-bg: #ffffff;
    --navy-deep: #020a2a;
    --navy-mid: #061a4f;
    --navy-glow: #0c2a72;
    --gold-light: #e3c27a;
    --gold: #b8904a;
    --gold-dark: #7a5a26;
    --ink-light: #ffffff;
    --ink-soft: #e9ecf5;
  }
  html, body {
    margin: 0;
    padding: 0;
    width: 1200px;
    height: 1200px;
    overflow: hidden;
    background: var(--page-bg);
  }
  .canvas {
    width: 1200px;
    height: 1200px;
    display: flex;
    align-items: center;
    justify-content: center;
  }
  .label {
    height: 1080px;
    width: auto;
    display: block;
  }
  .brand-name {
    font-family: "Zilla Slab", Georgia, serif;
    font-weight: 700;
    font-size: 78px;
    fill: var(--ink-light);
  }
  .brand-sub {
    font-family: "Zilla Slab", Georgia, serif;
    font-weight: 700;
    font-size: 33px;
    letter-spacing: 1.5px;
    fill: var(--ink-light);
  }
  .range-title {
    font-family: "Cormorant Garamond", Georgia, serif;
    font-weight: 500;
    font-size: 31px;
    letter-spacing: 4px;
    fill: var(--ink-soft);
  }
  .cask-line {
    font-family: "Oswald", "Arial Narrow", sans-serif;
    font-weight: 300;
    font-size: 42px;
    letter-spacing: 3px;
    fill: var(--ink-light);
  }
  .spec {
    font-family: "Lato", Arial, sans-serif;
    font-weight: 400;
    font-size: 22px;
    fill: var(--ink-light);
  }
</style>
</head>
<body>
<main class="canvas">
  <svg class="label" viewBox="0 0 430 1520" xmlns="http://www.w3.org/2000/svg" aria-label="Velinto Grand Reserva Brandy bottle label">
    <defs>
      <radialGradient id="label-bg" cx="50%" cy="45%" r="65%">
        <stop offset="0%" stop-color="var(--navy-glow)"/>
        <stop offset="55%" stop-color="var(--navy-mid)"/>
        <stop offset="100%" stop-color="var(--navy-deep)"/>
      </radialGradient>
      <linearGradient id="gold-rule" x1="0" y1="0" x2="1" y2="0">
        <stop offset="0%" stop-color="var(--gold-dark)"/>
        <stop offset="50%" stop-color="var(--gold-light)"/>
        <stop offset="100%" stop-color="var(--gold-dark)"/>
      </linearGradient>
      <linearGradient id="gold-field" x1="0" y1="1" x2="1" y2="0">
        <stop offset="0%" stop-color="var(--gold-dark)" stop-opacity="0.45"/>
        <stop offset="50%" stop-color="var(--gold)" stop-opacity="0.35"/>
        <stop offset="100%" stop-color="var(--gold-light)" stop-opacity="0.3"/>
      </linearGradient>
      <path id="cask-arc" d="M70,1160 Q215,1258 360,1160"/>
    </defs>

    <path class="label-shape" fill="url(#label-bg)"
      d="M0,42 Q0,2 40,2 L215,28 L390,2 Q430,2 430,42 L388,1478 Q387,1520 345,1520 L85,1520 Q43,1520 42,1478 Z"/>

    <g class="brand-lockup" text-anchor="middle">
      <text class="brand-name" x="215" y="178">Velinto</text>
      <text class="brand-sub" x="212" y="236">SWISS</text>
      <text class="brand-sub" x="212" y="271">DISTILLERY</text>
    </g>

    <g class="range">
      <rect x="70" y="362" width="290" height="2" fill="url(#gold-rule)"/>
      <text class="range-title" x="215" y="401" text-anchor="middle">GRAND RESERVA</text>
      <rect x="70" y="415" width="290" height="2" fill="url(#gold-rule)"/>
    </g>

    <rect class="product-lettering" x="140" y="490" width="170" height="590" rx="20"
      fill="url(#gold-field)" role="img" aria-label="Gold hand-lettered word Brandy set vertically"/>

    <text class="cask-line" text-anchor="middle">
      <textPath href="#cask-arc" startOffset="50%">CASK STRENGHT</textPath>
    </text>

    <g class="specs">
      <text class="spec" x="203" y="1422" text-anchor="end">25%</text>
      <rect x="214" y="1394" width="1.5" height="36" fill="var(--ink-light)"/>
      <text class="spec" x="226" y="1422">350ml</text>
    </g>
  </svg>
</main>
</body>
</html>
```